Fun relaxed Travel Photography Business Card*

Require a fun, funky and quirky but rememberable business card for a travel photographer

Industry/Entity Type

Photographer

Contact Information for Business Card

Front Card

(my name) Lenn D.

Travel Photographer ( small under travel photographer) “self-proclaimed”

(website logo) wanderingsoflenn.net

(Pixelgram logo) @wanderings_of_lenn

(Pixelgram logo) @wanderings_of_lenn_2.0 (backup for when Pixelgram puts Lenn on timeout for bad behaviour)

Tel: N/A (removing the potential awkwardness of me not replying)

Email: (see above)

Back Card

Offending people since 1986

(Bottom right corner) “p.s. travelling made me fatTER”

Font styles to use
Serif

Colors

Designer to choose colors to be used in the design.

Requirements
Must have
• a camera
• a similar cartoon version of me as the "logo" see attached files, try to make as similar as possible

```html
<!DOCTYPE html>
<html lang="en">
<head>
<meta charset="utf-8">
<title>Lenn D. – Travel Photographer Business Card</title>
<link href="https://fonts.googleapis.com/css2?family=Kaushan+Script&family=Oswald:wght@400&family=Varela+Round&family=Gochi+Hand&display=swap" rel="stylesheet">
<style>
  :root {
    --bg: #d3d3d3;
    --green: #00803a;
    --red: #dc0024;
    --yellow: #f2c521;
    --ink: #1b1b1b;
    --deep-green: #12351c;
    --mint: #cfe9c8;
    --white: #ffffff;
    --grey: #dedede;
  }
  * { margin: 0; padding: 0; box-sizing: border-box; }
  html, body { width: 1200px; height: 1200px; overflow: hidden; background: var(--bg); }
  .stage {
    position: relative; width: 1264px; height: 1264px;
    transform: scale(0.9494); transform-origin: 0 0;
  }
  .card { position: absolute; top: 243px; width: 444px; height: 777px; overflow: hidden; }
  .card--front { left: 69px; background: var(--green); }
  .card--back { left: 702px; background: var(--red); }

  .band { position: absolute; left: 0; width: 100%; bottom: 0; }
  .band--front {
    height: 150px; background: linear-gradient(180deg, var(--red), #c9001f);
    border-top: 8px solid var(--yellow);
  }
  .band--back {
    height: 230px; background: linear-gradient(180deg, var(--yellow), #efbf18);
    border-top: 8px solid var(--green);
  }

  .name {
    position: absolute; top: 36px; left: 0; width: 100%; text-align: center;
    font-family: "Kaushan Script", cursive; font-weight: 400; font-size: 74px;
    color: var(--white); line-height: 1;
  }
  .title {
    position: absolute; top: 142px; width: 100%; text-align: center;
    font-family: "Oswald", sans-serif; font-weight: 400; font-size: 28px;
    letter-spacing: 1px; color: var(--white); line-height: 1;
  }
  .subtitle {
    position: absolute; top: 176px; width: 100%; text-align: center;
    font-family: "Varela Round", sans-serif; font-size: 24px; color: var(--deep-green); line-height: 1;
  }
  .contacts { position: absolute; left: 81px; top: 250px; width: 350px; list-style: none; }
  .contact { display: flex; align-items: flex-start; gap: 14px; margin-bottom: 10px;
    font-family: "Gochi Hand", cursive; }
  .contact__icon { width: 24px; height: 24px; flex: none; }
  .contact__text { font-size: 22px; color: var(--mint); line-height: 26px; }
  .contact__note { display: block; font-size: 16px; color: var(--white); line-height: 18px; }
  .contact--plain .contact__text { font-size: 16px; color: var(--white); line-height: 18px; }
  .contact--gap { margin-top: 34px; }
  .plane-art {
    position: absolute; left: 161px; top: 492px; width: 190px; height: 180px;
    background: linear-gradient(135deg, var(--grey), #bfbfbf); border-radius: 24px;
  }

  .portrait {
    position: absolute; left: 68px; top: 40px; width: 306px; height: 306px; border-radius: 50%;
    border: 7px solid var(--ink);
    background: radial-gradient(circle at 50% 40%, #fdf1b8, #f3cd55);
  }
  .camera-art {
    position: absolute; left: 172px; top: 357px; width: 102px; height: 78px; border-radius: 10px;
    background: linear-gradient(#e6e6e6, #9c9c9c);
  }
  .tagline {
    position: absolute; top: 442px; width: 100%; text-align: center;
    font-family: "Kaushan Script", cursive; color: var(--white); line-height: 1;
  }
  .tagline__main { display: block; font-size: 42px; }
  .tagline__year { display: block; font-size: 32px; margin-top: 8px; }
  .postscript {
    position: absolute; left: 36px; top: 628px;
    font-family: "Gochi Hand", cursive; font-size: 30px; line-height: 42px; color: var(--ink);
    letter-spacing: 1px;
  }
</style>
</head>
<body>
<main class="stage">

  <section class="card card--front">
    <div class="band band--front" role="img" aria-label="Decorative red and yellow splash band"></div>

    <h1 class="name">Lenn D.</h1>
    <p class="title">TRAVEL PHOTOGRAPHER</p>
    <p class="subtitle">self-proclaimed</p>

    <ul class="contacts">
      <li class="contact">
        <svg class="contact__icon" viewBox="0 0 24 24" aria-hidden="true">
          <circle cx="12" cy="12" r="10" fill="none" stroke="var(--white)" stroke-width="2"/>
          <ellipse cx="12" cy="12" rx="4.5" ry="10" fill="none" stroke="var(--white)" stroke-width="1.5"/>
          <line x1="2" y1="12" x2="22" y2="12" stroke="var(--white)" stroke-width="1.5"/>
        </svg>
        <span class="contact__text">wanderingsoflenn.net</span>
      </li>
      <li class="contact">
        <svg class="contact__icon" viewBox="0 0 24 24" aria-hidden="true">
          <rect x="2" y="2" width="20" height="20" rx="5" fill="var(--white)"/>
        </svg>
        <span class="contact__text">@wanderings_of_lenn</span>
      </li>
      <li class="contact">
        <svg class="contact__icon" viewBox="0 0 24 24" aria-hidden="true">
          <rect x="2" y="2" width="20" height="20" rx="5" fill="var(--white)"/>
        </svg>
        <span class="contact__text">@wanderings_of_lenn_2.0
          <span class="contact__note">(backup for when Pixelgram puts<br>Lenn on timeout for bad behaviour)</span>
        </span>
      </li>
      <li class="contact contact--plain contact--gap">
        <svg class="contact__icon" viewBox="0 0 24 24" aria-hidden="true">
          <rect x="6" y="1" width="12" height="22" rx="2" fill="none" stroke="var(--white)" stroke-width="2"/>
          <line x1="10" y1="19" x2="14" y2="19" stroke="var(--white)" stroke-width="1.5"/>
        </svg>
        <span class="contact__text">N/A (removing the potential<br>awkwardness of me not replying)</span>
      </li>
      <li class="contact contact--plain">
        <svg class="contact__icon" viewBox="0 0 24 24" aria-hidden="true">
          <rect x="1" y="5" width="22" height="14" fill="var(--white)"/>
          <polyline points="1,5 12,13 23,5" fill="none" stroke="var(--green)" stroke-width="1.5"/>
        </svg>
        <span class="contact__text">(see above)</span>
      </li>
    </ul>

    <div class="plane-art" role="img" aria-label="Illustration of a white passenger plane flying upward"></div>
  </section>

  <section class="card card--back">
    <div class="band band--back" role="img" aria-label="Decorative yellow and green splash band"></div>

    <div class="portrait" role="img" aria-label="Cartoon portrait of the photographer in sunglasses and a floral shirt"></div>
    <div class="camera-art" role="img" aria-label="Illustration of a retro camera hanging on a strap"></div>

    <p class="tagline">
      <span class="tagline__main">Offending people</span>
      <span class="tagline__year">since 1986</span>
    </p>
    <p class="postscript">PS. traveling<br>made me fatTER</p>
  </section>

</main>
</body>
</html>
```